Fenwick yard services house wash and water tank cleaning trailer

Fenwick yard services is an exterior cleaning company, we have built a new trailer for cleaning water tanks and buildings. We would like a design that incorporates our company name, logo, phone number and web page. The trailer has 11 aluminum panels on it as you will see in the pics, we would like a design that brings it all together. The front 2 corner panels get a bit dirty, so our thought were we might be able to have a design that makes the front of the trailer look dirty and the rest look clean. For example a mud splash in the background on the front panels and maybe the front side panels and then the rest of the panels looking like they are soaped up or clean. www.fenwickyardservices.co.nz for details

Requirements
Must have
• A design that is eye catching
Nice to have
• some use of our company colors ( see pics or website ) www.fenwickyardsrevices.co.nz

Website across the rear of the trailer
Should not have
• plain design

```html
<!DOCTYPE html>
<html lang="en">
<head>
<meta charset="utf-8">
<title>Fenwick Yard Services – Trailer Panel Layout</title>
<link rel="stylesheet" href="https://fonts.googleapis.com/css2?family=Stardos+Stencil:wght@700&family=Inconsolata:wght@500&family=Roboto:wght@400;500&display=swap">
<style>
  :root {
    --brand-orange: #f58d21;
    --brand-blue: #0b7dcf;
    --sky-light: #dcefff;
    --ink: #1a1a1a;
    --grass-top: #9be14a;
    --grass-base: #3f9d12;
    --mud: #7a4a26;
    --outline: #b8b8b8;
    --label: #2b2b2b;
    --bg: #ffffff;
  }
  html, body { margin: 0; padding: 0; overflow: hidden; background: var(--bg); }
  .sheet { display: block; width: 1200px; height: 801px; }
  .stencil { font-family: "Stardos Stencil", "Rockwell", serif; font-weight: 700; fill: var(--ink); }
  .web-address { font-family: "Inconsolata", "Consolas", monospace; font-weight: 500; fill: var(--ink); }
  .body-text { font-family: "Roboto", Arial, sans-serif; fill: var(--ink); }
  .tagline { font-family: "Roboto", Arial, sans-serif; font-weight: 500; fill: var(--ink); }
  .dimension { font-family: "Roboto", Arial, sans-serif; font-size: 24px; fill: var(--label); }
  .band-orange { fill: var(--brand-orange); }
  .band-blue { fill: var(--brand-blue); }
  .panel-edge { fill: none; stroke: var(--ink); stroke-width: 3; }
  .panel-frame { fill: none; stroke: var(--outline); stroke-width: 3; }
  .logo-square { fill: var(--ink); }
  .social-dot { fill: var(--brand-blue); }
</style>
</head>
<body>
<svg class="sheet" viewBox="0 0 2340 1562" xmlns="http://www.w3.org/2000/svg" aria-label="Fenwick Yard Services trailer panel set">
  <defs>
    <linearGradient id="sky-fade" x1="0" y1="0" x2="0" y2="1">
      <stop offset="0" stop-color="#8cc6f0"/>
      <stop offset="1" stop-color="#ffffff"/>
    </linearGradient>
    <linearGradient id="sky-panel" x1="0" y1="0" x2="0" y2="1">
      <stop offset="0" stop-color="#1f86d6"/>
      <stop offset="0.55" stop-color="#a9d4f3"/>
      <stop offset="1" stop-color="#ffffff"/>
    </linearGradient>
    <linearGradient id="grass" x1="0" y1="0" x2="0" y2="1">
      <stop offset="0" stop-color="#d8f5b0" stop-opacity="0.2"/>
      <stop offset="0.35" stop-color="#9be14a"/>
      <stop offset="1" stop-color="#3f9d12"/>
    </linearGradient>
    <linearGradient id="tank" x1="0" y1="0" x2="1" y2="0">
      <stop offset="0" stop-color="#0a5fb8"/>
      <stop offset="0.45" stop-color="#2f9af0"/>
      <stop offset="1" stop-color="#0a5fb8"/>
    </linearGradient>
    <linearGradient id="mud" x1="0" y1="0" x2="0" y2="1">
      <stop offset="0" stop-color="#7a4a26" stop-opacity="0"/>
      <stop offset="0.5" stop-color="#8a5630" stop-opacity="0.7"/>
      <stop offset="1" stop-color="#6b3f1f"/>
    </linearGradient>
  </defs>

  <!-- Rear panels -->
  <g class="rear-left-panel">
    <rect class="band-blue" x="125" y="101" width="316" height="22"/>
    <rect class="band-orange" x="125" y="123" width="316" height="87"/>
    <rect x="125" y="210" width="316" height="60" fill="url(#sky-fade)"/>
  </g>
  <g class="rear-centre-panel">
    <rect class="band-blue" x="528" y="101" width="1347" height="22"/>
    <rect class="band-orange" x="528" y="123" width="1347" height="87"/>
    <rect x="528" y="210" width="1347" height="60" fill="url(#sky-fade)"/>
    <text class="stencil" x="1201" y="195" font-size="74" text-anchor="middle" letter-spacing="3">FENWICK YARD SERVICES</text>
    <text class="web-address" x="1225" y="255" font-size="52" text-anchor="middle">www.fenwickyardservices.co.nz</text>
  </g>
  <g class="rear-right-panel">
    <rect class="band-blue" x="1949" y="101" width="317" height="22"/>
    <rect class="band-orange" x="1949" y="123" width="317" height="87"/>
    <rect x="1949" y="210" width="317" height="60" fill="url(#sky-fade)"/>
    <circle class="social-dot" cx="1978" cy="176" r="14"/>
    <text class="tagline" x="2000" y="186" font-size="30">Linkora</text>
    <circle class="social-dot" cx="2112" cy="176" r="14"/>
    <text class="tagline" x="2134" y="186" font-size="30">Chirpnet</text>
  </g>
  <text class="dimension" x="1199" y="80" text-anchor="middle">2325 mm</text>
  <text class="dimension" x="2128" y="296" text-anchor="middle">550 mm</text>
  <text class="dimension" transform="translate(2306 175) rotate(-90)" text-anchor="middle">295 mm</text>

  <!-- Upper side panels -->
  <g class="side-upper-left">
    <rect class="logo-square" x="418" y="388" width="73" height="73"/>
    <polygon class="band-orange" points="675,370 1148,370 1059,459 675,459"/>
    <text class="stencil" x="688" y="430" font-size="54">FENWICK</text>
    <text class="stencil" x="688" y="453" font-size="28">YARD SERVICES</text>
    <polygon role="img" aria-label="Grass blades" points="398,466 1054,466 985,538 398,538" fill="url(#grass)"/>
    <polyline class="panel-edge" points="398,368 1150,368 985,538 398,538"/>
  </g>
  <g class="side-upper-right">
    <polygon class="band-orange" points="1254,375 2005,375 2005,467 1345,467"/>
    <text class="tagline" x="1965" y="443" font-size="38" text-anchor="end">Your Exterior Property Specialists</text>
    <polygon role="img" aria-label="Grass blades" points="1347,470 2005,470 2005,545 1420,545" fill="url(#grass)"/>
    <polyline class="panel-edge" points="2005,373 1252,373 1420,545 2005,545"/>
  </g>
  <text class="dimension" x="619" y="347" text-anchor="middle">1305 mm</text>
  <text class="dimension" transform="translate(380 425) rotate(-90)" text-anchor="middle">270 mm</text>
  <text class="dimension" x="627" y="572" text-anchor="middle">1037 mm</text>

  <!-- Lower side panels -->
  <g class="side-lower-left">
    <rect class="logo-square" x="428" y="635" width="63" height="62"/>
    <polygon class="band-orange" points="651,633 1125,633 1058,700 651,700"/>
    <text class="stencil" x="662" y="692" font-size="64">FENWICK</text>
    <polygon role="img" aria-label="Grass blades" points="398,703 1056,703 985,779 398,779" fill="url(#grass)"/>
    <polyline class="panel-edge" points="398,609 1150,609 985,779 398,779"/>
  </g>
  <g class="side-lower-right">
    <polygon class="band-orange" points="1268,633 1998,633 1998,700 1335,700"/>
    <text class="stencil" x="1657" y="688" font-size="52" text-anchor="middle" letter-spacing="2">YARD SERVICES</text>
    <polygon role="img" aria-label="Grass blades" points="1337,703 1998,703 1998,785 1413,785" fill="url(#grass)"/>
    <polyline class="panel-edge" points="1998,614 1247,614 1413,785 1998,785"/>
  </g>
  <text class="dimension" x="619" y="823" text-anchor="middle">1305 mm</text>
  <text class="dimension" transform="translate(380 667) rotate(-90)" text-anchor="middle">270 mm</text>

  <!-- Phone strip -->
  <rect class="band-orange" x="443" y="872" width="308" height="40"/>
  <rect class="band-orange" x="1631" y="869" width="309" height="40"/>
  <g class="phone-strip">
    <rect class="band-orange" x="901" y="845" width="592" height="91"/>
    <circle cx="952" cy="890" r="28" fill="none" stroke="var(--ink)" stroke-width="5"/>
    <path d="M940 874 q-6 4 -2 16 q6 14 18 18 q8 2 12 -4 l-8 -8 l-6 4 q-8 -4 -10 -12 l4 -6 z" fill="var(--ink)"/>
    <text class="stencil" x="1000" y="918" font-size="78" letter-spacing="4">21 555 0142</text>
  </g>
  <text class="dimension" x="1222" y="826" text-anchor="middle">1030 mm</text>
  <text class="dimension" transform="translate(1526 890) rotate(-90)" text-anchor="middle">160 mm</text>

  <!-- Front-left tank panel -->
  <g class="panel-water-tank">
    <rect x="85" y="999" width="392" height="506" fill="url(#sky-panel)"/>
    <rect class="band-blue" x="85" y="999" width="392" height="17"/>
    <rect class="band-orange" x="85" y="1016" width="392" height="62"/>
    <text class="stencil" x="112" y="1043" font-size="30">WATER TANK</text>
    <text class="stencil" x="112" y="1071" font-size="30">CLEANING</text>
    <circle cx="116" cy="1094" r="4" fill="var(--ink)"/>
    <text class="body-text" x="131" y="1101" font-size="19">Water Tank Clean</text>
    <circle cx="116" cy="1127" r="4" fill="var(--ink)"/>
    <text class="body-text" x="131" y="1134" font-size="19">Water Tank Clean &amp; Sanitize</text>
    <rect role="img" aria-label="Blue water tank" x="165" y="1185" width="245" height="300" rx="30" fill="url(#tank)"/>
    <rect role="img" aria-label="Grass blades" x="85" y="1420" width="392" height="85" fill="url(#grass)"/>
    <rect class="panel-frame" x="85" y="999" width="392" height="506"/>
  </g>
  <text class="dimension" x="300" y="991" text-anchor="middle">682 mm</text>
  <text class="dimension" transform="translate(80 1255) rotate(-90)" text-anchor="middle">880 mm</text>
  <text class="dimension" transform="translate(502 1255) rotate(-90)" text-anchor="middle">850 mm</text>

  <!-- Left corner panel -->
  <g class="corner-left">
    <polygon points="662,993 787,1338 790,1480 662,1480" fill="url(#sky-panel)"/>
    <polygon role="img" aria-label="Grass blades" points="662,1400 789,1400 790,1480 662,1480" fill="url(#grass)"/>
    <polygon class="panel-frame" points="662,993 787,1338 790,1480 662,1480"/>
  </g>
  <text class="dimension" transform="translate(652 1260) rotate(-90)" text-anchor="middle">840 mm</text>
  <text class="dimension" transform="translate(748 1160) rotate(70)" text-anchor="middle">580 mm</text>
  <text class="dimension" transform="translate(820 1410) rotate(-90)" text-anchor="middle">260 mm</text>
  <text class="dimension" x="728" y="1511" text-anchor="middle">210 mm</text>

  <!-- Front centre panels -->
  <g class="front-centre-upper">
    <rect x="917" y="991" width="461" height="330" fill="url(#sky-panel)"/>
    <rect class="logo-square" x="993" y="1011" width="89" height="88"/>
    <text class="stencil" x="1142" y="1166" font-size="66" text-anchor="middle">FENWICK</text>
    <rect class="band-orange" x="917" y="1174" width="461" height="51"/>
    <text class="stencil" x="1147" y="1212" font-size="34" text-anchor="middle" letter-spacing="1">YARD SERVICES</text>
    <text class="tagline" x="1146" y="1252" font-size="24" text-anchor="middle">Your Exterior Property Specialists</text>
    <circle class="band-orange" cx="982" cy="1285" r="19" stroke="var(--ink)" stroke-width="3"/>
    <text class="stencil" x="1015" y="1304" font-size="50" letter-spacing="3">21 555 0142</text>
    <rect class="panel-frame" x="917" y="991" width="461" height="330"/>
  </g>
  <g class="front-centre-lower">
    <rect role="img" aria-label="Grass blades with a light mud splash" x="917" y="1370" width="461" height="102" fill="url(#grass)"/>
    <rect class="panel-frame" x="917" y="1330" width="461" height="142"/>
  </g>
  <text class="dimension" x="1145" y="986" text-anchor="middle">770 mm</text>
  <text class="dimension" transform="translate(1418 1190) rotate(-90)" text-anchor="middle">550 mm</text>
  <text class="dimension" transform="translate(1418 1400) rotate(-90)" text-anchor="middle">285 mm</text>

  <!-- Right corner panel -->
  <g class="corner-right">
    <polygon points="1651,993 1651,1480 1523,1480 1527,1338" fill="url(#sky-panel)"/>
    <polygon role="img" aria-label="Grass with mud splash" points="1525,1390 1651,1390 1651,1480 1523,1480" fill="url(#mud)"/>
    <polygon class="panel-frame" points="1651,993 1651,1480 1523,1480 1527,1338"/>
  </g>
  <text class="dimension" transform="translate(1681 1410) rotate(-90)" text-anchor="middle">260 mm</text>
  <text class="dimension" x="1587" y="1511" text-anchor="middle">210 mm</text>

  <!-- Front-right services panel -->
  <g class="panel-exterior-cleaning">
    <rect x="1830" y="988" width="392" height="505" fill="url(#sky-panel)"/>
    <rect role="img" aria-label="Mud splash over grass" x="1840" y="1290" width="380" height="203" fill="url(#mud)"/>
    <rect class="band-blue" x="1830" y="988" width="392" height="18"/>
    <rect class="band-orange" x="1830" y="1006" width="392" height="62"/>
    <text class="stencil" x="1858" y="1032" font-size="30">EXTERIOR PROPERTY</text>
    <text class="stencil" x="1858" y="1062" font-size="30">CLEANING</text>
    <g class="body-text" font-size="19">
      <text x="1872" y="1095">Water Blasting</text>
      <text x="1872" y="1128">House Washing / Soft wash</text>
      <text x="1872" y="1161">Spouting/ Gutter Clearing</text>
      <text x="1872" y="1194">Deck Cleaning</text>
      <text x="1872" y="1227">Moss and Mould Treatment</text>
      <text x="1872" y="1260">Cleaning Driveways and Paths</text>
      <text x="1872" y="1293">Sanitize Playground Equipment</text>
      <text x="1872" y="1326">Sanitize Outdoor Seating</text>
      <text x="1872" y="1359">Clean Solar Panels</text>
      <text x="1872" y="1392">Fence Cleaning</text>
    </g>
    <g fill="var(--grass-base)">
      <circle cx="1859" cy="1253" r="3.5"/>
      <circle cx="1859" cy="1286" r="3.5"/>
      <circle cx="1859" cy="1319" r="3.5"/>
      <circle cx="1859" cy="1352" r="3.5"/>
      <circle cx="1859" cy="1385" r="3.5"/>
    </g>
    <rect class="panel-frame" x="1830" y="988" width="392" height="505"/>
  </g>
  <text class="dimension" x="2046" y="979" text-anchor="middle">682 mm</text>
  <text class="dimension" transform="translate(1826 1245) rotate(-90)" text-anchor="middle">880 mm</text>
  <text class="dimension" transform="translate(2250 1245) rotate(-90)" text-anchor="middle">850 mm</text>
</svg>
</body>
</html>
```